Brightway Carpet and Tile cleaning Business card Design

I need a design that has the same feel as my van.
i would also like a prominent "Review us on facebook" somewhere, but not that it makes it look silly.
I would like the card to have a little bit of grey or black in the design as well.

It will need contact details
phone: 0455 817264
email: rkbrightwayclean@mailbox-example.com
website: www.brightwaycarpetandtilecleaning-example.com.au
facebook: /brightwaycarpetandtilecleaning

Industry/Entity Type

Business

Contact Information for Business Card

Phone number 0455817264
Email rkbrightwayclean@mailbox-example.com
Website www.brightwaycarpetandtilecleaning-example.com.au
Facebook/brightwaycarpetandtilecleaning

Colors
000000

Requirements
Must have
• Same feel as my van
• I want the card to stand out from the crowd
Nice to have
• Maybe include a tiny bit of a third colour? Grey's,blacks, orange?

```html
<!DOCTYPE html>
<html lang="en">
<head>
<meta charset="utf-8">
<title>Brightway Carpet and Tile Cleaning – Business Card</title>
<link href="https://fonts.googleapis.com/css2?family=Quicksand:wght@500;700&family=Nunito:wght@400;600&display=swap" rel="stylesheet">
<style>
  :root {
    --stage: #ece8e2;
    --card: #ffffff;
    --sky: #29c3f0;
    --sky-deep: #03a9dc;
    --leaf: #8cc63f;
    --ink: #1d1d1b;
    --slate: #5f6062;
    --bubble: #eef6fb;
  }
  * { box-sizing: border-box; margin: 0; padding: 0; }
  html, body { width: 1189px; height: 1200px; overflow: hidden; }
  body { background: var(--stage); position: relative; font-family: "Nunito", sans-serif; color: var(--ink); }

  .card {
    position: absolute;
    width: 763px;
    height: 435px;
    background: var(--card);
    border-radius: 20px;
    overflow: hidden;
    box-shadow: 0 6px 22px rgba(0,0,0,0.12);
  }
  .card--front { left: 316px; top: 131px; }
  .card--back { left: 121px; top: 647px; }

  .bubble-field {
    position: absolute; inset: 0;
    background: radial-gradient(ellipse at 50% 40%, var(--card) 0%, var(--bubble) 70%);
  }
  .wave { position: absolute; left: 0; top: 0; width: 763px; height: 435px; }

  .brand { position: absolute; text-align: center; }
  .brand__name {
    display: flex; align-items: center; justify-content: center; gap: 12px;
    font-family: "Quicksand", sans-serif; font-weight: 700; color: var(--sky-deep);
    line-height: 1;
  }
  .brand__dot { border-radius: 50%; background: var(--leaf); flex: none; }
  .brand__tagline {
    font-family: "Quicksand", sans-serif; font-weight: 500; color: var(--slate);
    letter-spacing: 0.16em; text-transform: uppercase; margin-top: 8px;
  }

  .card--front .brand { left: 0; width: 763px; top: 128px; }
  .card--front .brand__name { font-size: 72px; }
  .card--front .brand__dot { width: 22px; height: 22px; }
  .card--front .brand__tagline { font-size: 19px; }

  .website {
    position: absolute; left: 0; width: 763px; top: 280px;
    text-align: center; font-size: 19px; color: var(--ink);
  }

  .card--back .brand { left: 20px; width: 340px; top: 162px; }
  .card--back .brand__name { font-size: 52px; gap: 9px; }
  .card--back .brand__dot { width: 16px; height: 16px; }
  .card--back .brand__tagline { font-size: 13.5px; margin-top: 6px; }

  .divider {
    position: absolute; left: 383px; top: 66px; width: 1px; height: 260px;
    background: linear-gradient(var(--sky-deep), var(--slate));
  }

  .person { position: absolute; left: 411px; top: 76px; }
  .person__name { font-family: "Quicksand", sans-serif; font-weight: 700; font-size: 25px; color: var(--sky-deep); line-height: 1.1; }
  .person__role { font-size: 19px; line-height: 1.2; }

  .contacts { position: absolute; left: 411px; top: 228px; list-style: none; }
  .contacts li { display: flex; align-items: center; gap: 6px; font-size: 19px; line-height: 1; height: 26px; white-space: nowrap; }
  .contacts .icon { width: 20px; height: 20px; flex: none; border-radius: 3px; background: var(--leaf); display: flex; align-items: center; justify-content: center; }
  .contacts .icon svg { width: 14px; height: 14px; }
  .contacts .email { font-size: 17px; }
</style>
</head>
<body>

<section class="card card--front" aria-label="Business card front">
  <div class="bubble-field" role="img" aria-label="Faint pale blue bubble pattern"></div>
  <div class="brand">
    <div class="brand__name"><span>Brightway</span><span class="brand__dot"></span></div>
    <div class="brand__tagline">Carpet &amp; Tile Cleaning</div>
  </div>
  <p class="website">www.brightwaycarpetandtilecleaning-example.com.au</p>
  <svg class="wave" viewBox="0 0 763 435" aria-hidden="true">
    <defs>
      <linearGradient id="skyFront" x1="0" y1="0" x2="0" y2="1">
        <stop offset="0" stop-color="#2ec6f2"/><stop offset="1" stop-color="#02a6da"/>
      </linearGradient>
    </defs>
    <path d="M0 343 C150 390 250 418 390 405 C540 390 640 340 763 338 L763 435 L0 435 Z" fill="url(#skyFront)"/>
    <path d="M0 334 C140 378 240 404 380 396 C520 388 640 325 750 325 C640 330 530 382 390 400 C250 414 140 392 0 340 Z" fill="#8cc63f"/>
  </svg>
</section>

<section class="card card--back" aria-label="Business card back">
  <div class="brand">
    <div class="brand__name"><span>Brightway</span><span class="brand__dot"></span></div>
    <div class="brand__tagline">Carpet &amp; Tile Cleaning</div>
  </div>
  <div class="divider"></div>
  <div class="person">
    <p class="person__name">Ryan Kellaway</p>
    <p class="person__role">Managing/Director</p>
  </div>
  <ul class="contacts">
    <li><span class="icon"><svg viewBox="0 0 24 24"><path d="M6.6 10.8a15 15 0 0 0 6.6 6.6l2.2-2.2c.3-.3.7-.4 1-.2 1.1.4 2.3.6 3.6.6.6 0 1 .4 1 1V20c0 .6-.4 1-1 1A17 17 0 0 1 3 4c0-.6.4-1 1-1h3.5c.6 0 1 .4 1 1 0 1.3.2 2.5.6 3.6.1.3 0 .7-.2 1z" fill="#fff"/></svg></span>0455 817264</li>
    <li class="email"><span class="icon"><svg viewBox="0 0 24 24"><rect x="3" y="6" width="18" height="12" rx="1" fill="none" stroke="#fff" stroke-width="2"/><path d="M3 7l9 6 9-6" fill="none" stroke="#fff" stroke-width="2"/></svg></span>rkbrightwayclean@mailbox-example.com</li>
    <li><span class="icon"></span>/brightwaycarpetandtilecleaning</li>
  </ul>
  <svg class="wave" viewBox="0 0 763 435" aria-hidden="true">
    <defs>
      <linearGradient id="skyBack" x1="0" y1="0" x2="0" y2="1">
        <stop offset="0" stop-color="#2ec6f2"/><stop offset="1" stop-color="#02a6da"/>
      </linearGradient>
    </defs>
    <path d="M0 343 C150 390 250 418 390 405 C540 390 640 340 763 338 L763 435 L0 435 Z" fill="url(#skyBack)"/>
    <path d="M0 334 C140 378 240 404 380 396 C520 388 640 325 750 325 C640 330 530 382 390 400 C250 414 140 392 0 340 Z" fill="#8cc63f"/>
  </svg>
</section>

</body>
</html>
```